Salsa Company needs a bold label design

We need a 16 ounce jar label design for a new food product called Rio Dorado Fire Roasted Salsa. We would like to see designs that incorporate our brandmarks (files attached) and use the colors red (#cb1e27), vivid orange (#e99a10), white (#FFFFFF), and black(# 000000). We’re aiming for a bold, eye-catching salsa label that features stylized retro typography on a vibrant vivid orange background, evoking a handcrafted, small-batch feel with a touch of nostalgic heat and Southwest character. The label should specify that Rio Dorado is "Fire Roasted Salsa" and that it is "MEDIUM" heat. A nutritional label and UPC code should be included. The ingrediants should be specified as "Pobalano, jalapeno, guajillo and habanero peppers, tomatoes, lemon juice, red wine vinegar, beet powder, and salt." The front of the jar should include the weight (16 oz, 454 grams). A sample of the colors and look I want is included. Finally, the side panel should include the text that reads...

Our Story
At Rio Dorado, our mission is simple: to craft small-batch salsas using only real ingredients and bold peppers that bring the heat and the flavor.

Born in a home kitchen and perfected over time, Rio Dorado’s tale started with a love for spice and a passion for sharing great food. Every jar reflects that journey — crafted with care, refined through experience, and made to bring bold flavor to every table.

Rio Dorado — Real Heat. Real Flavor!

Target Market(s)

middle income to higher income consumers.

Industry/Entity Type

salsa industry (food products)

Font styles to use
Sans Serif

Colors
F0912C
F2A743
F7CA91
FBE8D2
FDF5EE
EB3D1F
EC4F4E
F09395
F8D3D4
FCEDEE

Requirements
Must have
• eye catching layout
Nice to have
• example jar image attached

```html
<!DOCTYPE html>
<html lang="en">
<head>
<meta charset="utf-8">
<title>Rio Dorado Fire Roasted Salsa – Jar Label</title>
<link href="https://fonts.googleapis.com/css2?family=Alfa+Slab+One&family=Roboto+Condensed:wght@400;700&display=swap" rel="stylesheet">
<style>
  :root{
    --red:#cb1e27;
    --red-deep:#9e1419;
    --orange:#e99a10;
    --gold:#f2b22a;
    --white:#ffffff;
    --black:#000000;
    --ink:#2a1608;
    --stage:#141414;
  }
  *{box-sizing:border-box;margin:0;padding:0}
  html,body{width:831px;height:1200px;overflow:hidden}
  body{background:var(--stage);font-family:"Roboto Condensed",sans-serif;color:var(--ink)}

  .label{position:absolute;left:20px;top:390px;width:791px;height:420px;background:var(--orange);overflow:hidden}
  .band{position:absolute;left:0;width:100%;background:var(--red)}
  .band--top{top:0;height:30px}
  .band--bottom{bottom:0;height:40px}
  .pattern-strip{position:absolute;left:0;width:100%;height:14px;
    background:linear-gradient(90deg,var(--red-deep),#e0552a 50%,var(--red-deep))}
  .pattern-strip--top{top:30px}
  .pattern-strip--bottom{bottom:40px}

  /* left side panel */
  .side{position:absolute;left:22px;top:60px;width:240px;font-size:8.6px;line-height:1.32}
  .company{font-weight:700;font-size:9px;text-transform:uppercase;letter-spacing:.3px;margin-bottom:8px}
  .story-title{font-weight:700;font-size:10px;margin-bottom:2px}
  .story p{margin-bottom:5px}
  .story .tagline{font-weight:700}
  .ingredients{margin-top:6px;background:var(--white);border:1px solid var(--ink);padding:5px 6px;font-size:8.3px}
  .ingredients b{font-weight:700}
  .refrigerate{position:absolute;left:22px;bottom:66px;font-family:"Alfa Slab One",serif;color:var(--red);font-size:12px;letter-spacing:.5px}

  /* front panel */
  .front{position:absolute;left:268px;top:44px;width:276px;height:322px;background:var(--gold);
    border-left:2px solid var(--red-deep);border-right:2px solid var(--red-deep);text-align:center}
  .natural{margin-top:14px;font-weight:700;font-size:11px;letter-spacing:1.5px;color:var(--ink)}
  .brand-name{font-family:"Alfa Slab One",serif;font-weight:400;color:var(--red);font-size:40px;line-height:1;margin-top:14px;white-space:nowrap}
  .product-name{font-family:"Alfa Slab One",serif;color:var(--red);font-size:27px;line-height:1.05;margin-top:22px}
  .batch{font-family:"Alfa Slab One",serif;color:var(--ink);font-size:15px;margin-top:14px;letter-spacing:.5px}
  .seal{width:60px;height:60px;border-radius:50%;background:var(--ink);border:3px solid var(--white);margin:18px auto 0}
  .weight-row{position:absolute;left:268px;bottom:0;width:276px;height:40px;display:flex;align-items:center;justify-content:center;gap:22px;color:var(--white);font-weight:700}
  .weight-row .heat{font-family:"Alfa Slab One",serif;font-size:18px;letter-spacing:1px}
  .weight-row .qty{font-size:12px}

  /* right side panel */
  .nutrition{position:absolute;left:566px;top:54px;width:200px;height:302px;background:var(--white);border:1.5px solid var(--black);padding:4px 6px;font-size:8.2px;line-height:1.3;color:var(--black)}
  .nutrition h2{font-family:"Alfa Slab One",serif;font-weight:400;font-size:19px;line-height:1;border-bottom:1px solid var(--black);padding-bottom:3px;margin-bottom:2px}
  .nutrition .row{display:flex;justify-content:space-between;border-bottom:.5px solid var(--black)}
  .nutrition .row.major{font-weight:700}
  .nutrition .row.sub{padding-left:9px}
  .nutrition .row.subsub{padding-left:18px}
  .nutrition .rule{border-bottom:5px solid var(--black)}
  .nutrition .rule-mid{border-bottom:3px solid var(--black)}
  .nutrition .calories{font-size:13px;font-weight:700}
  .nutrition .dv{text-align:right;font-weight:700;border-bottom:.5px solid var(--black)}
  .nutrition .footnote{font-size:6.8px;line-height:1.25;margin-top:3px}
</style>
</head>
<body>
  <main class="label">
    <div class="band band--top"></div>
    <div class="pattern-strip pattern-strip--top" role="img" aria-label="Decorative Southwest border pattern"></div>
    <div class="pattern-strip pattern-strip--bottom" role="img" aria-label="Decorative Southwest border pattern"></div>
    <div class="band band--bottom"></div>

    <section class="side">
      <p class="company">Mesa Verde Food Co.<br>Amarillo, Texas</p>
      <div class="story">
        <p class="story-title">Our Story</p>
        <p>At Rio Dorado, our mission is simple: to craft small-batch salsas using only real ingredients and bold peppers that bring the heat and the flavor.</p>
        <p>Born in a home kitchen and perfected over time, Rio Dorado’s tale started with a love for spice and a passion for sharing great food. Every jar reflects that journey — crafted with care, refined through experience, and made to bring bold flavor to every table.</p>
        <p class="tagline">Rio Dorado — Real Heat. Real Flavor!</p>
      </div>
      <p class="ingredients"><b>Ingredients:</b> Pobalano, jalapeno, guajillo and habanero peppers, tomatoes, lemon juice, red wine vinegar, beet powder, and salt.</p>
    </section>
    <p class="refrigerate">REFRIGERATE AFTER OPENING</p>

    <section class="front">
      <p class="natural">100% NATURAL</p>
      <h1 class="brand-name">Rio Dorado</h1>
      <p class="product-name">FIRE ROASTED<br>SALSA</p>
      <p class="batch">SMALL BATCH CRAFTED</p>
      <div class="seal" role="img" aria-label="Quality seal"></div>
    </section>
    <div class="weight-row">
      <span class="qty">16oz</span>
      <span class="heat">MEDIUM</span>
      <span class="qty">454g</span>
    </div>

    <section class="nutrition">
      <h2>Nutrition Facts</h2>
      <div class="row"><span>8 servings per container</span></div>
      <div class="row major rule"><span>Serving size</span><span>2 Tbsp (30g)</span></div>
      <div class="row major"><span>Amount per serving</span></div>
      <div class="row calories rule-mid"><span>Calories</span><span>10</span></div>
      <p class="dv">% Daily Value*</p>
      <div class="row major"><span>Total Fat 0g</span><span>0%</span></div>
      <div class="row sub"><span>Saturated Fat 0g</span><span>0%</span></div>
      <div class="row sub"><span>Trans Fat 0g</span><span></span></div>
      <div class="row major"><span>Cholesterol 0mg</span><span>0%</span></div>
      <div class="row major"><span>Sodium 115mg</span><span>5%</span></div>
      <div class="row major"><span>Total Carbohydrate 2g</span><span>1%</span></div>
      <div class="row sub"><span>Dietary Fiber 0g</span><span>0%</span></div>
      <div class="row sub"><span>Total Sugars 1g</span><span></span></div>
      <div class="row subsub"><span>Includes 0g Added Sugars</span><span>0%</span></div>
      <div class="row major rule"><span>Protein 0g</span><span></span></div>
      <div class="row"><span>Vitamin D 0mcg</span><span>0%</span></div>
      <div class="row"><span>Calcium 10mg</span><span>0%</span></div>
      <div class="row"><span>Iron 0.2mg</span><span>2%</span></div>
      <div class="row rule-mid"><span>Potassium 110mg</span><span>2%</span></div>
      <p class="footnote">*The % Daily Value tells you how much a nutrient in a serving contributes to a daily diet.</p>
    </section>
  </main>
</body>
</html>
```